The Linen Loft Co

We need a business card design for our wardrobe company.
Please visit our website www.gentlelinenlofts.com to get an idea of who we are.

```html
<!DOCTYPE html>
<html lang="en">
<head>
<meta charset="utf-8">
<title>The Linen Loft Co — Business Card</title>
<link rel="stylesheet" href="https://fonts.googleapis.com/css2?family=Lato:wght@400;700&display=swap">
<style>
  :root {
    --backdrop: #2b2b2b;
    --card: #0d0d0d;
    --card-edge: #1c1c1c;
    --ink: #f2f2f2;
    --ink-soft: #cfcfcf;
    --rule: #6a6a6a;
  }
  * { margin: 0; padding: 0; box-sizing: border-box; }
  html, body {
    width: 1200px; height: 900px; overflow: hidden;
    background: var(--backdrop);
    font-family: "Lato", sans-serif;
    color: var(--ink);
  }
  .canvas { position: relative; width: 1200px; height: 900px; }
  .card {
    position: absolute; left: 320px; width: 560px; height: 320px;
    background: linear-gradient(160deg, var(--card-edge), var(--card) 60%);
    border-radius: 4px;
  }
  .card--front { top: 100px; }
  .card--back { top: 480px; }

  .brand {
    position: absolute; left: 110px; top: 118px;
    display: flex; align-items: center; gap: 22px;
  }
  .brand__mark {
    flex: none; width: 84px; height: 84px; border: 2px solid var(--ink);
  }
  .brand__name {
    font-weight: 700; font-size: 19px; letter-spacing: 0.5px;
    text-transform: uppercase; white-space: nowrap;
  }
  .brand__tagline {
    font-size: 15px; margin-top: 4px; color: var(--ink-soft); white-space: nowrap;
  }

  .contact {
    position: absolute; inset: 0;
    display: flex; flex-direction: column; align-items: center; justify-content: center;
    text-align: center;
  }
  .contact__name {
    font-weight: 700; font-size: 20px; letter-spacing: 0.5px; text-transform: uppercase;
  }
  .contact__role { font-size: 14px; color: var(--ink-soft); margin-top: 2px; }
  .contact__icons { display: flex; align-items: center; gap: 6px; margin: 10px 0 8px; }
  .contact__icons::before, .contact__icons::after {
    content: ""; width: 46px; height: 1px; background: var(--rule);
  }
  .contact__icon {
    width: 20px; height: 20px; border-radius: 50%; background: var(--ink);
    display: flex; align-items: center; justify-content: center;
  }
  .contact__line { font-size: 15px; line-height: 1.35; white-space: nowrap; }
  .contact__divider { width: 150px; height: 1px; background: var(--rule); margin: 8px 0; }
</style>
</head>
<body>
<main class="canvas">
  <section class="card card--front" aria-label="Card front">
    <div class="brand">
      <span class="brand__mark"></span>
      <div>
        <p class="brand__name">The Linen Loft Co</p>
        <p class="brand__tagline">Fitted Around Your Life</p>
      </div>
    </div>
  </section>

  <section class="card card--back" aria-label="Card back">
    <div class="contact">
      <p class="contact__name">Daniel Hartley</p>
      <p class="contact__role">Managing Director</p>
      <div class="contact__icons">
        <span class="contact__icon">
          <svg width="12" height="12" viewBox="0 0 24 24"><path fill="#0d0d0d" d="M6.6 10.8a15 15 0 0 0 6.6 6.6l2.2-2.2a1 1 0 0 1 1-.25 11.4 11.4 0 0 0 3.6.6 1 1 0 0 1 1 1V20a1 1 0 0 1-1 1A17 17 0 0 1 3 4a1 1 0 0 1 1-1h3.5a1 1 0 0 1 1 1c0 1.25.2 2.450.6 3.6a1 1 0 0 1-.25 1z"/></svg>
        </span>
        <span class="contact__icon">
          <svg width="12" height="12" viewBox="0 0 24 24"><path fill="#0d0d0d" d="M3 5h18v14H3zm2 2v.5l7 4.5 7-4.5V7z"/></svg>
        </span>
        <span class="contact__icon">
          <svg width="12" height="12" viewBox="0 0 24 24"><path fill="#0d0d0d" d="M12 2a7 7 0 0 0-7 7c0 5 7 13 7 13s7-8 7-13a7 7 0 0 0-7-7zm0 9.5A2.5 2.5 0 1 1 12 6.5a2.5 2.5 0 0 1 0 5z"/></svg>
        </span>
      </div>
      <p class="contact__line">0207 555 0148</p>
      <p class="contact__line">info@gentlelinenlofts.com</p>
      <p class="contact__line">www.gentlelinenlofts.com</p>
      <span class="contact__divider"></span>
      <p class="contact__line">Marlow Yard, 24 Fenn Street</p>
      <p class="contact__line">London E9 4QZ</p>
    </div>
  </section>
</main>
</body>
</html>
```